Webdesign für Zahnarztpraxis
Zielgruppe
Zahnarztpraxis
Aufgabenstellung
- Klares und übersichtliches Desgin
- Nicht zu verspielt
- Informativ
- Leichte Naviagtion
- Das Design der alten Webseite soll NICHT kopiert werden
- Die Farben Blau und Grün aus dem Logo sollen sich wiederfinden
- Designbeispiele, die dem Kunden gefallen sind https://www.falkmann-ostrup-zahnarztpraxis.de/ und https://www.zahvilkorn.de/

```html
<!DOCTYPE html>
<html lang="de">
<head>
<meta charset="utf-8">
<title>Zahnpraxis Hellmer – Praxis &amp; Labor</title>
<link href="https://fonts.googleapis.com/css2?family=Poppins:wght@400;500;600&family=Lato:wght@400;700&display=swap" rel="stylesheet">
<style>
:root{
  --blue:#1e9ad6;
  --green:#6cb33f;
  --ink:#222;
  --text:#333;
  --white:#fff;
}
*{box-sizing:border-box;margin:0;padding:0}
html,body{width:1200px;height:2807px;overflow:hidden;background:var(--white)}
body{font-family:"Lato",sans-serif;color:var(--text);position:relative}
.abs{position:absolute}

.topbar{top:0;left:0;width:1200px;height:46px;background:var(--blue);color:var(--white);font-family:"Poppins",sans-serif;font-size:13px;font-weight:500}
.topbar .item{position:absolute;top:14px;display:flex;align-items:center;gap:9px}

.site-header{top:46px;left:0;width:1200px;height:131px;background:var(--white);border-bottom:1px solid #ddd}
.brand{position:absolute;left:102px;top:44px;display:flex;align-items:center;gap:10px;font-family:"Poppins",sans-serif;font-size:26px;font-weight:500;color:var(--blue)}
.brand .dot{width:28px;height:28px;border-radius:50%;background:var(--green)}
.nav{position:absolute;right:96px;top:78px;display:flex;gap:31px;font-family:"Poppins",sans-serif;font-size:15px;font-weight:500;color:var(--ink)}
.nav a{color:inherit;text-decoration:none;padding-bottom:5px}
.nav a.active{border-bottom:3px solid var(--green)}

.hero{top:177px;left:0;width:1200px;height:358px;background:linear-gradient(100deg,#c9c2b4 0%,#eef1f2 30%,#f4f6f6 60%,#dfe6e3 80%,#eef0f1 100%)}
.tag{position:absolute;color:var(--white);font-family:"Poppins",sans-serif;font-weight:500;font-size:22px;padding:5px 13px;line-height:1.3}
.tag.blue{left:87px;top:25px;background:var(--blue)}
.tag.green{left:116px;top:85px;background:var(--green)}
.notice{position:absolute;left:117px;top:155px;width:652px;height:186px;border:5px solid var(--green);background:rgba(255,255,255,.88);padding:18px 21px}
.notice h2{font-family:"Poppins",sans-serif;font-size:23px;font-weight:500;color:var(--ink)}
.notice .sub{font-family:"Poppins",sans-serif;font-size:14px;margin-bottom:24px}
.notice p{font-size:14px;line-height:1.3;color:var(--ink);margin-bottom:10px}

.feature{left:0;width:1200px}
.feature h2{font-family:"Poppins",sans-serif;font-size:23px;font-weight:500;color:var(--ink);margin-bottom:4px}
.feature .lead{font-family:"Poppins",sans-serif;font-size:15px;line-height:1.5}
.feature .body{font-size:14.5px;line-height:1.3;color:var(--ink);margin-top:42px}
.btn{display:inline-block;width:196px;height:41px;line-height:41px;text-align:center;background:var(--green);color:var(--white);font-family:"Poppins",sans-serif;font-size:15px;font-weight:500;text-decoration:none}
.photo{position:absolute}

.services{top:983px;left:0;width:1200px;height:462px;background:var(--blue);color:var(--white)}
.services h2{position:absolute;top:41px;width:100%;text-align:center;font-family:"Poppins",sans-serif;font-size:23px;font-weight:500}
.service{position:absolute;width:166px;text-align:center;font-family:"Poppins",sans-serif;font-size:15px;line-height:1.45;color:#e8f4fb}
.service svg{display:block;margin:0 auto 10px}
.more-box{position:absolute;left:991px;top:275px;width:120px;height:120px;border:2px solid var(--white);display:flex;align-items:center;justify-content:center;text-align:center;font-family:"Poppins",sans-serif;font-size:15px;line-height:1.45}

.footer{top:2302px;left:0;width:1200px;height:505px;background:var(--blue);color:var(--white);font-size:14.5px;line-height:1.25}
.fcol{position:absolute;top:44px}
.fcol h3{font-family:"Poppins",sans-serif;font-size:15px;font-weight:500;margin:20px 0 28px}
.fcol p{margin-bottom:18px}
.hours{display:grid;grid-template-columns:80px auto}
.hours.wide{grid-template-columns:84px auto}
.fcol a{color:var(--white)}
.legal{position:absolute;left:100px;top:470px;display:flex;gap:26px;font-family:"Poppins",sans-serif;font-size:15px;color:#d8ecf8}
</style>
</head>
<body>

<header class="abs topbar">
  <div class="item" style="left:787px">
    <svg width="22" height="16" viewBox="0 0 22 16" fill="none" stroke="#fff" stroke-width="2"><rect x="1" y="1" width="20" height="14" rx="2"/><path d="M1 2l10 7 10-7"/></svg>
    info@zahnarztpraxis-hellmer.de
  </div>
  <div class="item" style="left:1067px">
    <svg width="20" height="20" viewBox="0 0 24 24" fill="none" stroke="#fff" stroke-width="2"><path d="M5 2h4l2 5-3 2a11 11 0 0 0 6 6l2-3 5 2v4a2 2 0 0 1-2 2A17 17 0 0 1 3 4a2 2 0 0 1 2-2z"/><path d="M14 2a8 8 0 0 1 8 8M14 6a4 4 0 0 1 4 4"/></svg>
    03741 / 58210
  </div>
</header>

<div class="abs site-header">
  <div class="brand"><span class="dot"></span>Zahnpraxis Hellmer</div>
  <nav class="nav">
    <a class="active" href="#">Unsere Praxis</a>
    <a href="#">Leistungen</a>
    <a href="#">Praxislabor</a>
    <a href="#">Team</a>
    <a href="#">Kontakt</a>
  </nav>
</div>

<section class="abs hero" role="img" aria-label="Heller Behandlungsraum mit Fenster und Regalen">
  <div class="tag blue">Herzlich Willkommen in unserer Praxis!</div>
  <div class="tag green">Ihr Wohlbefinden ist unser Anspruch.</div>
  <div class="notice">
    <h2>Wichtige Information</h2>
    <div class="sub">für unsere Patienten</div>
    <p>in der Zeit von xx.xx.2025 - einschließlich xx.xx.2025 bleibt unsere Praxis geschlossen.</p>
    <p>Die Vertretung in dieser Zeit übernimmt Frau/Herr ... Bitte melden Sie sich im Vorfeld<br>telefonisch an.</p>
  </div>
</section>

<section class="abs feature" style="top:535px;height:448px">
  <div class="abs" style="left:100px;top:124px;width:400px">
    <h2>Unsere Praxis</h2>
    <div class="lead">Praxis &amp; Dentallabor in Lindenbach-Oberau.</div>
    <div class="body">Prävention und Individualprophylaxe in jeder Altersgruppe!<br>Zahnärztin spricht auch fließend Englisch.</div>
    <a class="btn" href="#" style="margin-top:34px">Mehr erfahren</a>
  </div>
  <div class="photo" role="img" aria-label="Behandlungszimmer mit Zahnarztstuhl und Pflanze" style="left:521px;top:38px;width:580px;height:371px;background:linear-gradient(135deg,#f1f4f5,#dfe7ea 55%,#c7d3d6)"></div>
</section>

<section class="abs services">
  <h2>Unsere Leistungen</h2>
  <svg width="0" height="0" style="position:absolute">
    <defs>
      <g id="tooth-plus" fill="none" stroke="#fff" stroke-width="2.6" stroke-linecap="round" stroke-linejoin="round">
        <path d="M10 14c0-8 8-11 15-8 3 1 5 1 8 0 7-3 15 0 15 8 0 9-5 14-6 22-1 10-2 28-7 28-4 0-4-20-8-20s-4 20-8 20c-5 0-6-18-7-28-1-8-6-13-6-22z"/>
        <circle cx="57" cy="21" r="11" fill="#1e9ad6"/>
        <path d="M57 15v12M51 21h12"/>
      </g>
    </defs>
  </svg>
  <div class="service" style="left:134px;top:96px"><svg width="80" height="72" viewBox="0 0 72 68"><use href="#tooth-plus"/></svg>Zahnärztliche Diagnostik</div>
  <div class="service" style="left:293px;top:96px"><svg width="80" height="72" viewBox="0 0 72 68" fill="none" stroke="#fff" stroke-width="2.6" stroke-linecap="round" stroke-linejoin="round"><path d="M10 14c0-8 8-11 15-8 3 1 5 1 8 0 7-3 15 0 15 8 0 9-5 14-6 22-1 10-2 28-7 28-4 0-4-20-8-20s-4 20-8 20c-5 0-6-18-7-28-1-8-6-13-6-22z"/><path d="M47 11l10-4 10 4v8c0 7-5 11-10 13-5-2-10-6-10-13z" fill="#1e9ad6"/><path d="M52 19l4 4 6-7"/></svg>Individualprophylaxe</div>
  <div class="service" style="left:466px;top:96px"><svg width="100" height="72" viewBox="0 0 90 68" fill="none" stroke="#fff" stroke-width="2.6" stroke-linecap="round" stroke-linejoin="round"><path d="M10 14c0-8 8-11 15-8 3 1 5 1 8 0 7-3 15 0 15 8 0 9-5 14-6 22-1 10-2 28-7 28-4 0-4-20-8-20s-4 20-8 20c-5 0-6-18-7-28-1-8-6-13-6-22z"/><path d="M30 22l56 20-2 4-56-18z" fill="#1e9ad6"/><path d="M32 22l4-9M37 24l4-9M42 26l4-9M47 28l4-9"/></svg>Professionelle Zahnreinigung</div>
  <div class="service" style="left:632px;top:96px"><svg width="80" height="72" viewBox="0 0 72 68"><use href="#tooth-plus"/></svg>Konservierende Zahnheilkunde</div>
  <div class="service" style="left:799px;top:96px"><svg width="80" height="72" viewBox="0 0 72 68"><use href="#tooth-plus"/></svg>Zahnärztliche Prothetik</div>
  <div class="service" style="left:965px;top:96px"><svg width="80" height="72" viewBox="0 0 72 68"><use href="#tooth-plus"/></svg>Kieferorthopädie</div>

  <div class="service" style="left:134px;top:281px"><svg width="80" height="72" viewBox="0 0 72 68"><use href="#tooth-plus"/></svg>Chirurgische Zahnheilkunde</div>
  <div class="service" style="left:300px;top:281px"><svg width="80" height="72" viewBox="0 0 72 68"><use href="#tooth-plus"/></svg>Ästhetische Zahnheilkunde</div>
  <div class="service" style="left:466px;top:281px"><svg width="80" height="72" viewBox="0 0 72 68"><use href="#tooth-plus"/></svg>Ganzheitliche Zahnheilkunde</div>
  <div class="service" style="left:632px;top:281px"><svg width="80" height="72" viewBox="0 0 72 68"><use href="#tooth-plus"/></svg>Kinderzahnheilkunde</div>
  <div class="service" style="left:799px;top:281px"><svg width="80" height="72" viewBox="0 0 72 68"><use href="#tooth-plus"/></svg>Bioverträglicher Zahnersatz</div>
  <a class="more-box" href="#" style="color:#fff;text-decoration:none">Mehr<br>erfahren</a>
</section>

<section class="abs feature" style="top:1445px;height:425px">
  <div class="abs" style="left:100px;top:123px;width:400px">
    <h2>Unser Praxislabor</h2>
    <div class="lead">Unsere Praxis verfügt über ein eigenes Praxislabor.</div>
    <a class="btn" href="#" style="margin-top:92px">Mehr erfahren</a>
  </div>
  <div class="photo" role="img" aria-label="Wartebereich mit Stühlen und Blumengesteck" style="left:521px;top:37px;width:580px;height:371px;background:linear-gradient(120deg,#eef0ee,#cfc6b8 45%,#8f6a55 75%,#a77d6b)"></div>
</section>

<section class="abs feature" style="top:1870px;height:432px">
  <div class="photo" role="img" aria-label="Praxisteam in weißer Kleidung im Grünen" style="left:102px;top:23px;width:579px;height:371px;background:linear-gradient(180deg,#6f8a55,#a8b89a 40%,#eef1f3 60%,#f6f7f8)"></div>
  <div class="abs" style="left:732px;top:128px;width:380px">
    <h2>Unser Praxisteam</h2>
    <div class="lead">kompetent, herzlich und darauf fokussiert, Ihre Zahngesundheit bestmöglich zu unterstützen.</div>
    <a class="btn" href="#" style="margin-top:87px">Mehr erfahren</a>
  </div>
</section>

<footer class="abs footer">
  <div class="fcol" style="left:100px;width:320px">
    <svg width="24" height="30" viewBox="0 0 24 30"><path d="M12 0C5 0 0 5 0 12c0 8 12 18 12 18s12-10 12-18C24 5 19 0 12 0z" fill="#fff"/><circle cx="12" cy="11" r="4" fill="#1e9ad6"/></svg>
    <h3>So erreichen Sie uns</h3>
    <p>Weidenstraße 14<br>08527 Lindenbach-Oberau</p>
    <p>Telefon: 03741-58210<br>Fax: 03741-58219</p>
    <p>E-Mail: info@zahnarztpraxis-hellmer.de</p>
  </div>
  <div class="fcol" style="left:469px;width:260px">
    <svg width="30" height="30" viewBox="0 0 30 30" fill="none" stroke="#fff" stroke-width="2.2"><circle cx="15" cy="15" r="13"/><path d="M15 7v8l5 4"/></svg>
    <h3>Unsere Öffnungszeiten</h3>
    <div class="hours wide" style="margin-bottom:18px">
      <span>Montag:</span><span>9:00 bis 13:00 Uhr und<br>14:00 bis 19:00 Uhr</span>
      <span>Dienstag:</span><span>9:00 bis 13:00 Uhr und<br>14:00 bis 19:00 Uhr</span>
      <span>Mittwoch:</span><span>9:00 bis 14:00 Uhr</span>
      <span>Donnerstag:</span><span>geschlossen</span>
      <span>Freitag:</span><span>9:00 bis 13:00 Uhr</span>
    </div>
    <p>... und nach Vereinbarung</p>
    <p>Infomieren Sie sich bitte hier über Aktualisierungen auf unserem Praxis-Eintrag bei Findora.</p>
  </div>
  <div class="fcol" style="left:823px;width:290px">
    <svg width="30" height="30" viewBox="0 0 24 24" fill="none" stroke="#fff" stroke-width="1.8"><path d="M5 2h4l2 5-3 2a11 11 0 0 0 6 6l2-3 5 2v4a2 2 0 0 1-2 2A17 17 0 0 1 3 4a2 2 0 0 1 2-2z"/><path d="M14 2a8 8 0 0 1 8 8M14 6a4 4 0 0 1 4 4"/></svg>
    <h3>Telefonzeiten</h3>
    <p>Innerhalb dieser Zeiten sind wir für Sie telefonisch erreichbar:</p>
    <div class="hours" style="margin-bottom:18px">
      <span>Montag:</span><span>9:00 bis 15:00 Uhr</span>
      <span>Dienstag:</span><span>9:00 bis 15:00 Uhr</span>
      <span>Mittwoch:</span><span>9:00 bis 12:00 Uhr</span>
    </div>
    <p>In dringenden Fällen wenden Sie sich bitte an zahnärtlichen Notdienst.</p>
    <p>Link 'zur Notdienstsuche' <a href="#">https://<br>www.zahnnotdienst-region.de/patienten/<br>notdienstsuche/</a></p>
  </div>
  <div class="legal"><span>Impressum</span><span>Datenschutz</span><span>AGB</span></div>
</footer>

</body>
</html>
```